revised: 'kelvale ironworks' logo -or- business card

we require a business card or a logo that can be used on a business card & other stationery

(i've just recently decided to open this contest up to logo designs as well - but if you have already been working on a card concept, please feel free to continue with it & submit!)

-

We design and build custom brackets and fixings for our customers and their castles, i.e. homes, offices, workshops, farms etc. Our products might be used to:
- brace or support structures, such as houses, decks, small bridges, etc.
- connect any building material to another
- or could simply be a unique piece that exists as a talking point

As part of our design process we would produce drawings/plans/blue prints/prototypes of the product. Our designs factor in multiple elements, from the materials being joined, the client's taste, and the overall durability demanded by the application - if necessary, the bracket may also be endorsed by a third party, such as a stuctural or mechanical engineer.

The build process takes part in our workshop and on the client's site - some elements may be manufactured off-site, depending on the design chosen and the materials used.

Our brackets are designed to our customers' tastes and could be made to be hidden within the structure or exposed to create interest. Our brackets can be large or small, or be neat with clean lines or take on more of an industrial look.
Updates

please note brief has been updated with a more specific description of our business activity

i have also added the final drawing that was used to water-jet the bracket shown in the photos

also, you will note i changed the title to 'logo + business card'

i don't expect a logo as a discrete artefact of the job, however, i expect that some or all elements on the face of the business card will lend themselves to the street sign (as stated in the original brief) as well as any future logo used on letter heads, invoices, etcetera

another update - changed the allowable entries to include logo's only, as well as business cards

Industry/Entity Type

Industrial

Requirements
Must have
• the face should have the name 'Kelvale Ironworks' (or no/all-caps)

the number '75' in the logo, which will also be turned into a conservative (residential) street sign ('75' being a street number) - '75' should stand alone -OR- be readily identified by someone who has previously received a business card

i need to make this '75' and any associated 'framing', so it should be transferrable to cad/dxf for machining, laser/water-cutting, brazing/welding, etcet.

(on that note, the winning designer will be able to share their vision for this sign and we'll adhere to it ... within the realms of possibility! if you're happy with the result then you could include it in your portfolio)
Nice to have
• one side of the card needs a majority of space for quotes, hand-written information, etcet. so this side should be white or a light, complimentary colour suitable for black/blue pen

the following should appear somewhere on the card (there is no email or website) :
- name : Dana Morrow (Proprietor)
- mobile phone number : +61 (0) 498 761203
- abn: 58 904 617 235

any combination of the following (or equivalent) text:

* 'your castle' - this is slang for your house/place (i prefer this to 'home' as 1: it can apply to a place of business, and 2: for me at least, it conjurs images of wrought iron, brass, hardwood & stone)

* unique

* ...

```html
<!DOCTYPE html>
<html lang="en">
<head>
<meta charset="utf-8">
<title>Kelvale Ironworks – Business Card</title>
<link rel="stylesheet" href="https://fonts.googleapis.com/css2?family=Arimo:wght@400;700&family=Pinyon+Script&display=swap">
<style>
  :root {
    --page: #fdfdfd;
    --card-light: #ebebeb;
    --navy: #00466e;
    --steel: #9aa8b3;
    --text-grey: #6b6b6b;
    --white: #ffffff;
  }
  * { box-sizing: border-box; margin: 0; padding: 0; }
  html, body {
    width: 807px;
    height: 1200px;
    overflow: hidden;
    background: var(--page);
  }
  .canvas {
    position: relative;
    width: 807px;
    height: 1200px;
  }
  .card {
    position: absolute;
    top: 557px;
    width: 255px;
    height: 169px;
    border-radius: 5px;
    overflow: hidden;
  }
  .card--front { left: 171px; background: var(--card-light); }
  .card--back  { left: 433px; background: var(--navy); }

  .brand {
    position: absolute;
    left: 22px;
    top: 15px;
    display: flex;
    align-items: center;
    gap: 4px;
  }
  .brand__dot {
    width: 22px;
    height: 22px;
    border-radius: 50%;
    background: var(--steel);
  }
  .brand__name {
    font-family: "Arimo", Arial, sans-serif;
    font-size: 12px;
    line-height: 12px;
    font-weight: 400;
    color: var(--navy);
  }

  .person {
    position: absolute;
    left: 84px;
    top: 62px;
    width: 100px;
    text-align: center;
  }
  .person__name {
    font-family: "Pinyon Script", cursive;
    font-size: 21px;
    line-height: 20px;
    color: var(--text-grey);
    white-space: nowrap;
  }
  .person__role {
    font-family: "Arimo", Arial, sans-serif;
    font-size: 5.5px;
    letter-spacing: 2.4px;
    color: var(--text-grey);
  }
  .contact {
    position: absolute;
    left: 79px;
    top: 95px;
    font-family: "Arimo", Arial, sans-serif;
    font-size: 8px;
    line-height: 10px;
    color: var(--text-grey);
  }
  .contact__label { display: inline-block; width: 21px; }

  .wave {
    position: absolute;
    left: 0;
    bottom: 0;
    width: 255px;
    height: 44px;
  }
  .wave__navy { fill: var(--navy); }
  .wave__steel { fill: var(--steel); }

  .emblem {
    position: absolute;
    left: 50%;
    top: 50%;
    transform: translate(-50%, -50%);
    display: flex;
    flex-direction: column;
    align-items: center;
    gap: 8px;
  }
  .emblem__disc {
    width: 76px;
    height: 76px;
    border-radius: 50%;
    background: var(--steel);
  }
  .emblem__name {
    font-family: "Arimo", Arial, sans-serif;
    font-size: 10px;
    color: var(--white);
    white-space: nowrap;
  }
</style>
</head>
<body>
<main class="canvas">
  <section class="card card--front" aria-label="Business card front">
    <div class="brand">
      <span class="brand__dot"></span>
      <span class="brand__name">Kelvale<br>ironworks</span>
    </div>
    <div class="person">
      <p class="person__name">Dana Morrow</p>
      <p class="person__role">PROPRIETOR</p>
    </div>
    <div class="contact">
      <p>Mobile: +61 (0) 498 761203</p>
      <p><span class="contact__label">abn</span>:&nbsp; 58 904 617 235</p>
    </div>
    <svg class="wave" viewBox="0 0 255 44" preserveAspectRatio="none" aria-hidden="true">
      <path class="wave__navy" d="M0 14 C60 4 120 8 170 16 C210 22 235 22 255 18 L255 44 L0 44 Z"/>
      <path class="wave__steel" d="M0 28 C50 18 110 18 160 28 C200 35 230 34 255 30 L255 44 L0 44 Z"/>
    </svg>
  </section>

  <section class="card card--back" aria-label="Business card back">
    <div class="emblem">
      <span class="emblem__disc"></span>
      <span class="emblem__name">Kelvale Ironworks</span>
    </div>
  </section>
</main>
</body>
</html>
```